QVR business card

Need a business card for a company that provides instructional design and elearning development services. The website is here: http://quorvane.studio/

I'm attaching a current logo, as well as the old business card design. While I like to keep it clean, the old design is too simplistic for my liking. The only idea I want to reuse from the old design is placing industry jargon on the back of the card, just need a better way to present it. But if you have other ideas for the back--feel free to experiment.

Please use the colors complementary to the color we have on the website. Thank you!

```html
<!DOCTYPE html>
<html lang="en">
<head>
<meta charset="utf-8">
<title>QVR business card</title>
<link rel="stylesheet" href="https://fonts.googleapis.com/css2?family=Fira+Sans+Condensed:wght@400;700;800&family=Arimo:wght@400;700&display=swap">
<style>
  :root {
    --teal: #14b2ae;
    --gold: #d6c98c;
    --white: #ffffff;
    --ink: #2b2b2b;
    --stage: #ecebe8;
  }
  * { margin: 0; padding: 0; box-sizing: border-box; }
  html, body { width: 1200px; height: 675px; overflow: hidden; }
  body {
    background: var(--stage);
    display: flex;
    align-items: center;
    justify-content: center;
    gap: 50px;
  }
  .card {
    position: relative;
    width: 530px;
    height: 303px;
    overflow: hidden;
    border-radius: 3px;
    box-shadow: 0 6px 18px rgba(0,0,0,.15);
  }

  /* Back of the card */
  .card-back {
    background: var(--teal);
    color: var(--white);
    font-family: "Fira Sans Condensed", sans-serif;
    display: flex;
    align-items: center;
    padding: 0 20px 0 26px;
  }
  .headline {
    font-weight: 800;
    font-size: 54px;
    line-height: .9;
    letter-spacing: .5px;
    padding-right: 14px;
    border-right: 2px solid var(--white);
  }
  .jargon {
    list-style: none;
    padding-left: 14px;
    font-size: 23px;
    line-height: 1.2;
    text-transform: uppercase;
    white-space: nowrap;
  }

  /* Front of the card */
  .card-front {
    background: var(--white);
    font-family: "Arimo", sans-serif;
    color: var(--ink);
  }
  .identity { position: absolute; left: 32px; top: 30px; }
  .person-name { color: var(--teal); font-weight: 700; font-size: 17px; }
  .person-role { font-size: 12px; margin-top: 2px; }
  .brand {
    position: absolute; right: 46px; top: 92px;
    display: flex; align-items: center; gap: 10px;
  }
  .brand-dot { width: 22px; height: 22px; border-radius: 50%; background: var(--teal); }
  .brand-name { font-weight: 700; font-size: 44px; color: var(--gold); letter-spacing: 1px; }
  .contacts { position: absolute; left: 32px; top: 128px; list-style: none; font-size: 13px; }
  .contacts li { display: flex; align-items: center; gap: 8px; margin-bottom: 6px; }
  .contact-icon { width: 14px; height: 14px; }
  .footer-band {
    position: absolute; left: 0; right: 0; bottom: 0;
    height: 48px;
    background: var(--teal);
    display: flex; align-items: center; justify-content: flex-end;
    padding-right: 28px;
  }
  .website { color: var(--white); font-size: 19px; letter-spacing: 1.5px; }
</style>
</head>
<body>
  <section class="card card-back">
    <h1 class="headline">HOW<br>CAN<br>WE<br>HELP?</h1>
    <ul class="jargon">
      <li>Mobile Learning SCORM</li>
      <li>Instructional Design LMS</li>
      <li>MOOCs eLearning HTML5</li>
      <li>Adult Learning Theory</li>
      <li>Gamification Classroom</li>
      <li>xAPI Blended Learning</li>
    </ul>
  </section>

  <section class="card card-front">
    <div class="identity">
      <p class="person-name">Daniel Marrow</p>
      <p class="person-role">Managing Director</p>
    </div>

    <div class="brand">
      <span class="brand-dot"></span>
      <span class="brand-name">QVR</span>
    </div>

    <ul class="contacts">
      <li>
        <svg class="contact-icon" viewBox="0 0 14 14"><rect width="14" height="14" rx="2" fill="var(--teal)"/><path d="M4 3.5c1 0 1.5 1.6 1 2.2-.4.4.9 2 1.8 2.6.5-.4 2 .3 2 1.2 0 .8-1 1.2-1.8 1-2-.6-4.2-3-4.4-5.2 0-1 .6-1.8 1.4-1.8z" fill="var(--white)"/></svg>
        <span>555-013-2047</span>
      </li>
      <li>
        <svg class="contact-icon" viewBox="0 0 14 14"><rect width="14" height="14" rx="2" fill="var(--teal)"/><rect x="3" y="4" width="8" height="6" fill="none" stroke="var(--white)" stroke-width="1"/><path d="M3 4l4 3.2L11 4" fill="none" stroke="var(--white)" stroke-width="1"/></svg>
        <span>dmarrow@quorvane.studio</span>
      </li>
    </ul>

    <div class="footer-band">
      <p class="website">www.quorvane.studio</p>
    </div>
  </section>
</body>
</html>
```